Luxury Wine Label for New Startup Winery

We need a wine label for our new winery startup. We have worked with a local designer but do not feel the resulting label / logo have the elevation required to present our brand as a luxury wine. Our winery is called "Quailbrook Vineyards" and we are focused on extremely high quality hand crafted artisan and estate wines from the Pacific Northwest.
We would like to see designs that utilize a tree line, or other imagery that represents the "Quailbrook" part of our company name. Another interesting feature could be wood grain.
A logo will be required based on your design so please design with this in mind:
This logo should be consistent with the wine bottle label design, and should be representative of our high end exclusive wine while giving a sense of place (Oregon/ Pacific Northwest.)
I will supply an image of the design we received from our local designer, PLEASE NOTE: in general we do like wood grain and tree line concepts but feel the execution was poorly done.
ATTN: Logo design should be suitable for use on: Bottles (Red wine/rose/white wine), Bussiness cards, vehicle signage, business signage, etc
P.S.:
If you have a design that is not outside the box we are still interested in seeing it.
Label is for a burgundy style bottle with a label height of 3.5 - 4" and a width of 3.5-4"
any label <= 4"x4" and >=3.5"x3.5" will be acceptable:
HOWEVER Width should be greater than or equal to height due to the bottle format
Target Market(s)
Wine enthusiasts with adequate discretionary budgets to afford $100 bottles of wine.
Industry/Entity Type
Wine / Winery
Requirements
Must have
- A sense of luxury, a feel of exclusivity, and a theme consistent with our product and brand name
Nice to have
- Tree line, wood grain or other wood themes. Serif fonts
Should not have
- anything cheesy, off topic, hard to read script fonts or anything that makes the label hard to read from a few feet away or too busy

```html
<!DOCTYPE html>
<html lang="en">
<head>
<meta charset="utf-8">
<title>Quailbrook Vineyards – Syrah Label</title>
<link href="https://fonts.googleapis.com/css2?family=Bodoni+Moda:wght@400;500&family=Libre+Caslon+Text&display=swap" rel="stylesheet">
<style>
  :root {
    --canvas: #ffffff;
    --label-black: #000000;
    --frame-grey: #9a918c;
    --gold: #f2d23a;
    --gold-deep: #d9a82a;
    --gold-muted: #d6a93a;
    --ivory: #ffffff;
    --wood-dark: #3a1a14;
    --wood-mid: #5a2c22;
    --wood-light: #6b3a2d;
  }
  * { margin: 0; padding: 0; box-sizing: border-box; }
  html, body {
    width: 1200px; height: 1000px; overflow: hidden;
    background: var(--canvas);
  }
  .canvas { position: relative; width: 1200px; height: 1000px; }

  .front-label {
    position: absolute; left: 188px; top: 58px;
    width: 824px; height: 669px;
    background: var(--label-black);
  }
  .front-label__frame {
    position: absolute; left: 51px; top: 51px;
    width: 722px; height: 567px;
    border: 2px solid var(--frame-grey);
  }
  .front-label__scene {
    position: absolute; left: 192px; top: 97px;
    width: 440px; height: 165px;
    background: radial-gradient(ellipse at 50% 55%, #f6dc4a 0%, #d9a82a 55%, rgba(0,0,0,0) 72%);
  }
  .wordmark {
    position: absolute; left: 0; right: 0;
    text-align: center;
    font-family: "Bodoni Moda", "Didot", serif;
    font-weight: 400;
    line-height: 1;
    white-space: nowrap;
  }
  .wordmark--name {
    top: 300px;
    font-size: 84px;
    color: var(--gold);
    letter-spacing: -1px;
    transform: scaleX(0.86);
  }
  .wordmark--type {
    top: 380px;
    font-size: 78px;
    color: var(--ivory);
    letter-spacing: -1px;
    transform: scaleX(0.86);
  }
  .front-label__rule {
    position: absolute; left: 188px; top: 490px;
    width: 447px; height: 2px;
    background: var(--ivory);
  }
  .appellation {
    position: absolute; left: 0; right: 0; top: 528px;
    text-align: center;
    font-family: "Libre Caslon Text", "Georgia", serif;
    font-size: 37px;
    color: var(--ivory);
    line-height: 1;
  }

  .varietal-band {
    position: absolute; left: 187px; top: 756px;
    width: 825px; height: 180px;
    background: linear-gradient(90deg, var(--wood-mid) 0%, var(--wood-dark) 18%, var(--wood-light) 35%, var(--wood-mid) 52%, var(--wood-dark) 70%, var(--wood-light) 86%, var(--wood-mid) 100%);
  }
  .varietal-band__frame {
    position: absolute; left: 26px; top: 26px;
    width: 774px; height: 129px;
    border: 2px solid var(--gold-muted);
  }
  .varietal-band__name {
    position: absolute; left: 0; right: 0; top: 54px;
    text-align: center;
    font-family: "Bodoni Moda", "Didot", serif;
    font-size: 78px;
    letter-spacing: 8px;
    line-height: 1;
    color: var(--gold-muted);
  }
</style>
</head>
<body>
<main class="canvas">
  <section class="front-label">
    <div class="front-label__frame"></div>
    <div class="front-label__scene" role="img" aria-label="Gold illustration of a tree line of evergreens on a hill between mountain peaks, with birds in flight"></div>
    <h1>
      <span class="wordmark wordmark--name">QUAILBROOK</span>
      <span class="wordmark wordmark--type">VINEYARDS</span>
    </h1>
    <div class="front-label__rule"></div>
    <p class="appellation">Willamette Valley</p>
  </section>

  <section class="varietal-band" role="img" aria-label="Dark wood grain band">
    <div class="varietal-band__frame"></div>
    <p class="varietal-band__name">SYRAH</p>
  </section>
</main>
</body>
</html>
```